Automotive component supplier needs a business card design

We need a business card design for our company called Velran Global Components Ltd based in the UK. We are a supplier of interior and exterior components to premium car manufacturers such as Corvel Ashby, Hadley Fenn, Marquist and Tavarelli. We would like to see a modern business card design that uses the colour blue.

Target Market(s)

Premium automotive car manufacturers.

Industry/Entity Type

Automotive

Contact Information for Business Card

Company Name : Velran Global Components Limited
Address: 17 Marlow Yard, Upper Heath, Warwick, CV31 8QL, United Kingdom
Web Address : www.velrancomponents-example.co.uk

Font styles to use
Other font styles liked:
• Helvetica

Colors
3176b5
0255a3
85acd3
cfdeed
cee9f5
85cae6
34a6d7
0692cd
9bcb3c

Requirements
Must have
• Clear company logo and a mixture of blue colours.
Nice to have
• A high quality modern image.
Should not have
• Multiple colours.

```html
<!DOCTYPE html>
<html lang="en">
<head>
<meta charset="utf-8">
<title>Velran Global Components – Business Card</title>
<link rel="stylesheet" href="https://fonts.googleapis.com/css2?family=Nunito+Sans:wght@400;600;700&display=swap">
<style>
  :root {
    --stage: #e6e7e8;
    --brand-blue: #0a8fcf;
    --accent-green: #9bcb3c;
    --paper: #ffffff;
    --rule: #3176b5;
    --shadow: rgba(0, 0, 0, 0.28);
  }
  * { margin: 0; padding: 0; box-sizing: border-box; }
  html, body {
    width: 1200px; height: 927px; overflow: hidden;
    background: var(--stage);
    font-family: "Nunito Sans", Helvetica, Arial, sans-serif;
  }
  .stage { position: relative; width: 1200px; height: 927px; }

  .card {
    position: absolute; top: 98px;
    width: 417px; height: 731px;
    border-radius: 14px; overflow: hidden;
    box-shadow: 8px 10px 12px var(--shadow);
  }
  .card--front { left: 163px; background: var(--paper); }
  .card--back  { left: 620px; background: var(--brand-blue); }

  .wordmark { position: absolute; left: 0; width: 100%; text-align: center; font-weight: 700; }
  .wordmark__name { display: block; font-size: 76px; line-height: 1; letter-spacing: 3px; }
  .wordmark__line { display: block; font-size: 20px; letter-spacing: 5.5px; margin-top: 2px; }
  .card--front .wordmark { top: 48px; color: var(--brand-blue); }
  .card--back .wordmark { top: 316px; color: var(--paper); }

  .person { position: absolute; top: 314px; left: 0; width: 100%; text-align: center; }
  .person__name { font-size: 27px; font-weight: 700; color: var(--brand-blue); letter-spacing: 1.2px; line-height: 1; }
  .person__role {
    display: flex; align-items: center; margin-top: 5px;
    font-size: 17px; color: var(--accent-green);
  }
  .person__role::before, .person__role::after { content: ""; flex: 1; height: 1px; background: var(--rule); }
  .person__role span { padding: 0 4px; }

  .contact { position: absolute; left: 0; width: 100%; text-align: center; color: var(--brand-blue); font-size: 18px; line-height: 23px; font-style: normal; }
  .contact--address { top: 474px; }
  .contact--lines { top: 587px; }
  .contact__icons { position: absolute; top: 558px; left: 0; width: 100%; display: flex; justify-content: center; gap: 6px; }
  .contact__icons svg { width: 12px; height: 12px; }

  .foot-band { position: absolute; left: 0; bottom: 0; width: 100%; height: 26px; display: flex; }
  .foot-band__end { width: 65px; background: var(--accent-green); }
  .foot-band__mid { flex: 1; }
  .card--front .foot-band__mid { background: var(--brand-blue); }
  .card--back .foot-band__mid { background: var(--paper); }
</style>
</head>
<body>
<main class="stage">
  <section class="card card--front" aria-label="Card front">
    <div class="wordmark">
      <span class="wordmark__name">VELRAN</span>
      <span class="wordmark__line">GLOBAL COMPONENTS</span>
    </div>

    <div class="person">
      <p class="person__name">MAREK ELLISON</p>
      <p class="person__role"><span>Director</span></p>
    </div>

    <address class="contact contact--address">
      17 Marlow Yard<br>
      Upper Heath, Warwick<br>
      CV31 8QL, United Kingdom
    </address>

    <div class="contact__icons" aria-hidden="true">
      <svg viewBox="0 0 12 12"><path d="M2.5 1l2 2.2-1 1.3c.7 1.5 1.6 2.4 3 3l1.3-1 2.2 2-1 1.5C5 10 2 7 1 2.5z" fill="#9bcb3c"/></svg>
      <svg viewBox="0 0 12 12"><rect x="3" y="0.8" width="6" height="10.4" rx="1" fill="none" stroke="#9bcb3c" stroke-width="1.2"/><circle cx="6" cy="9.3" r="0.7" fill="#9bcb3c"/></svg>
      <svg viewBox="0 0 12 12"><rect x="1" y="2.5" width="10" height="7" fill="none" stroke="#9bcb3c" stroke-width="1.2"/><path d="M1 2.5l5 4 5-4" fill="none" stroke="#9bcb3c" stroke-width="1.2"/></svg>
      <svg viewBox="0 0 12 12" fill="none" stroke="#9bcb3c" stroke-width="1"><circle cx="6" cy="6" r="5"/><ellipse cx="6" cy="6" rx="2.2" ry="5"/><path d="M1 6h10M2 3.5h8M2 8.5h8"/></svg>
    </div>

    <div class="contact contact--lines">
      <p>+330 5550-1426</p>
      <p>+330 5550-2873</p>
      <p>info@velrancomponents-example.co.uk</p>
      <p>www.velrancomponents-example.co.uk</p>
    </div>

    <div class="foot-band"><span class="foot-band__end"></span><span class="foot-band__mid"></span><span class="foot-band__end"></span></div>
  </section>

  <section class="card card--back" aria-label="Card back">
    <div class="wordmark">
      <span class="wordmark__name">VELRAN</span>
      <span class="wordmark__line">GLOBAL COMPONENTS</span>
    </div>
    <div class="foot-band"><span class="foot-band__end"></span><span class="foot-band__mid"></span><span class="foot-band__end"></span></div>
  </section>
</main>
</body>
</html>
```